Blue Heron Journeys

We are a predominantly online travel agency with high-end (first/business class) clients. I'm looking to either have our existing logo revamped or a new logo created with business card layout. I prefer to work with existing logo if possible so it remains familiar with existing clientele. I have uploaded a yellow business card layout showing icons on one side of the card. I would like to keep my existing colours, not yellow. could the company name/tag line go over the icons?
Industry/Entity Type
Business
Contact Information for Business Card
Lucinda Fairley
Director
(I.A.T.A. 07715463)
(Corvano Pty. Ltd) ABN 61 574 203 918
512/18 Kendrick Lane
Wattle Reach | NSW 2577 | Australia
www.blueheronjourneys.com.au
m: + 61 (0) 417 588 130
t: + 61 (0) 2 9416 2058
e: lucinda@blueheronjourneys.com.au

```html
<!DOCTYPE html>
<html lang="en">
<head>
<meta charset="utf-8">
<title>Blue Heron Journeys – Business Card</title>
<link href="https://fonts.googleapis.com/css2?family=Roboto:ital,wght@0,400;1,400&family=Roboto+Condensed:wght@400;700&display=swap" rel="stylesheet">
<style>
  :root {
    --backdrop: #2b2b2b;
    --card-white: #fdfdfb;
    --ink: #111111;
    --ink-soft: #4a4a4a;
    --divider: #9a9a9a;
    --panel-blue: #dce8f3;
    --panel-blue-deep: #c8dbed;
    --back-base-1: #eef3f8;
    --back-base-2: #dde8f3;
    --edge-band: #5a5a5a;
  }
  * { box-sizing: border-box; margin: 0; padding: 0; }
  html, body {
    width: 1200px; height: 960px; overflow: hidden;
    background: var(--backdrop);
  }
  .canvas { position: relative; width: 1200px; height: 960px; }

  .card { position: absolute; width: 600px; }
  .card--front {
    left: 314px; top: 113px; height: 342px;
    background: var(--card-white);
  }
  .card--back {
    left: 311px; top: 472px; height: 343px;
  }

  .brand-panel {
    position: absolute;
    display: flex; align-items: center; justify-content: center;
  }
  .brand-panel__fill { position: absolute; inset: 0; }
  .brand-name {
    position: relative;
    font-family: "Roboto", sans-serif;
    font-weight: 400;
    color: var(--ink);
    white-space: nowrap;
  }
  .card--front .brand-panel { left: 50px; top: 122px; width: 261px; height: 100px; }
  .card--front .brand-panel__fill { background: var(--panel-blue); }
  .card--front .brand-name { font-size: 23px; }

  .divider {
    position: absolute; left: 328px; top: 62px;
    width: 1px; height: 225px; background: var(--divider);
  }

  .contact { position: absolute; left: 362px; top: 72px; width: 232px; }
  .contact__name {
    font-family: "Roboto Condensed", sans-serif; font-weight: 700;
    font-size: 21px; color: var(--ink); line-height: 24px;
  }
  .contact__role {
    font-family: "Roboto Condensed", sans-serif; font-weight: 400;
    font-size: 15px; color: var(--ink-soft); line-height: 20px;
  }
  .contact__address {
    margin-top: 11px;
    font-family: "Roboto", sans-serif; font-size: 13px;
    color: var(--ink-soft); line-height: 18px; white-space: nowrap;
  }
  .contact__list { list-style: none; margin-top: 10px; }
  .contact__item {
    display: flex; align-items: center; gap: 9px;
    font-family: "Roboto", sans-serif; font-size: 13px;
    color: var(--ink-soft); line-height: 19px; white-space: nowrap;
  }
  .contact__icon { width: 14px; height: 14px; flex: none; fill: var(--ink); }

  .edge-band {
    position: absolute; left: 0; bottom: 0; width: 600px; height: 14px;
    background: var(--edge-band);
  }

  .back-fill {
    position: absolute; inset: 0;
    background: linear-gradient(90deg, var(--back-base-1), var(--back-base-2) 50%, var(--back-base-1));
  }
  .card--back .brand-panel { left: 157px; top: 122px; width: 276px; height: 109px; }
  .card--back .brand-panel__fill { background: var(--panel-blue-deep); }
  .card--back .brand-name { font-size: 24px; }
  .back-url {
    position: absolute; left: 0; right: 0; top: 262px;
    text-align: center;
    font-family: "Roboto", sans-serif; font-style: italic;
    font-size: 15px; letter-spacing: 3px; color: var(--ink-soft);
  }
</style>
</head>
<body>
<main class="canvas">

  <section class="card card--front" aria-label="Business card front">
    <div class="brand-panel">
      <div class="brand-panel__fill" role="img" aria-label="Soft blue striped panel behind the company name"></div>
      <span class="brand-name">Blue Heron Journeys</span>
    </div>

    <div class="divider"></div>

    <div class="contact">
      <p class="contact__name">LUCINDA FAIRLEY</p>
      <p class="contact__role">DIRECTOR</p>
      <p class="contact__address">512/18 Kendrick Lane<br>Wattle Reach | NSW 2577 | Australia</p>
      <ul class="contact__list">
        <li class="contact__item">
          <svg class="contact__icon" viewBox="0 0 24 24"><path d="M6.6 10.8a15.1 15.1 0 0 0 6.6 6.6l2.2-2.2c.3-.3.7-.4 1-.2 1.1.4 2.3.6 3.6.6.6 0 1 .4 1 1V20c0 .6-.4 1-1 1C10.6 21 3 13.4 3 4c0-.6.4-1 1-1h3.5c.6 0 1 .4 1 1 0 1.3.2 2.5.6 3.6.1.3 0 .7-.2 1z"/></svg>
          + 61 (0) 2 9416 2058
        </li>
        <li class="contact__item">
          <svg class="contact__icon" viewBox="0 0 24 24"><path d="M7 1h10a2 2 0 0 1 2 2v18a2 2 0 0 1-2 2H7a2 2 0 0 1-2-2V3a2 2 0 0 1 2-2zm0 3v14h10V4z"/></svg>
          + 61 (0) 417 588 130
        </li>
        <li class="contact__item">
          <svg class="contact__icon" viewBox="0 0 24 24"><path d="M5 3h14v18H5zm3 4v2h8V7zm0 4v2h8v-2zm0 4v2h5v-2z"/></svg>
          ABN 61 574 203 918
        </li>
        <li class="contact__item">
          <svg class="contact__icon" viewBox="0 0 24 24"><path d="M2 5h20v14H2zm2 2v.5l8 5 8-5V7l-8 5z"/></svg>
          lucinda@blueheronjourneys.com.au
        </li>
        <li class="contact__item">
          <svg class="contact__icon" viewBox="0 0 24 24"><path d="M12 2a10 10 0 1 0 0 20 10 10 0 0 0 0-20zm-1 17.9A8 8 0 0 1 4.2 10L9 14.8v1a2 2 0 0 0 2 2zm6.9-2.5A2 2 0 0 0 16 16h-1v-3a1 1 0 0 0-1-1H8v-2h2a1 1 0 0 0 1-1V7h2a2 2 0 0 0 2-2v-.4a8 8 0 0 1 2.9 12.8z"/></svg>
          www.blueheronjourneys.com.au
        </li>
      </ul>
    </div>

    <div class="edge-band" role="img" aria-label="Striped edge band"></div>
  </section>

  <section class="card card--back" aria-label="Business card back">
    <div class="back-fill" role="img" aria-label="Pale blue striped background"></div>
    <div class="brand-panel">
      <div class="brand-panel__fill" role="img" aria-label="Blue striped panel behind the company name"></div>
      <span class="brand-name">Blue Heron Journeys</span>
    </div>
    <p class="back-url">www.blue heron journeys.com.au</p>
  </section>

</main>
</body>
</html>
```